A resume/portfolio website for myself

I'm an independent software contractor, architect, tech trainer. I need a web site to present myself. Many ready to use portfolio designs are too artistic and focused on presenting design skills of the person. I like a nice website but the content should be a little less graphic than if you would present a graphic designer. Content could be presentation of me, core skill qualities and services and resume. Potentially a page with my tech courses in the longer run

```html
<!DOCTYPE html>
<html lang="en">
<head>
<meta charset="utf-8">
<title>Daniel Storm – Software Contractor</title>
<link href="https://fonts.googleapis.com/css2?family=Mulish:wght@400;600;700;800&display=swap" rel="stylesheet">
<style>
:root{
  --navy:#0f1a3c;
  --navy-soft:#2b3c6e;
  --orange:#ee7623;
  --ink:#2a2a2a;
  --muted:#6b6b6b;
  --panel:#f1f1f1;
  --ring:#c9c9c9;
  --white:#ffffff;
}
*{box-sizing:border-box;margin:0;padding:0}
html,body{width:1200px;height:3864px;overflow:hidden}
body{font-family:"Mulish",Arial,sans-serif;color:var(--ink);background:var(--white);position:relative}
.hero{position:absolute;left:0;top:0;width:1200px;height:170px;background:linear-gradient(90deg,#34476f,#4a5f8a 40%,#3b4f7a 70%,#2e3f66)}
.btn{display:inline-flex;align-items:center;gap:8px;background:var(--orange);color:var(--white);font-weight:700;font-size:15px;letter-spacing:.5px;padding:12px 26px;border-radius:26px;text-transform:uppercase}
.btn svg{width:14px;height:14px}
.hero .btn{position:absolute;right:130px;top:100px}
.avatar{position:absolute;left:512px;top:148px;width:176px;height:176px;border-radius:50%;border:6px solid var(--white);background:radial-gradient(circle at 50% 40%,#c8b8a8,#8a7a6e);box-shadow:0 2px 8px rgba(0,0,0,.2)}
.intro{position:absolute;top:370px;left:0;width:1200px;text-align:center}
.name{font-size:31px;font-weight:800;letter-spacing:1px;color:var(--ink)}
.tagline{font-size:19px;color:var(--muted);margin-top:22px}
.intro p.body{width:860px;margin:28px auto 0;font-size:14.5px;line-height:1.75;color:var(--muted)}
.contact{display:flex;justify-content:center;gap:38px;font-size:17px;font-weight:700;margin-top:30px}
.contact span{display:inline-flex;align-items:center;gap:10px}
.contact svg{width:18px;height:18px;fill:var(--orange)}
.social{display:flex;justify-content:center;gap:10px;margin-top:30px}
.social i{display:block;width:40px;height:40px;border-radius:50%;background:var(--navy-soft)}
.social i:nth-child(2){background:#2a9fd6}.social i:nth-child(3){background:#c62f2f}.social i:nth-child(4){background:#a0704b}.social i:nth-child(5){background:#2b6ea8}
.panel{position:absolute;left:140px;width:920px;background:var(--panel)}
.tab{position:absolute;left:50%;transform:translateX(-50%);top:0;background:var(--navy);color:var(--white);font-size:30px;font-weight:700;letter-spacing:1px;padding:10px 44px;white-space:nowrap}
.work{top:900px;height:1120px}
.timeline{position:absolute;left:0;top:0;width:100%;height:100%}
.timeline .axis{position:absolute;left:380px;top:160px;width:5px;height:1000px;background:var(--orange)}
.job{position:absolute;left:0;width:100%}
.job .role{position:absolute;left:100px;font-size:19px;font-weight:800}
.job .dates{position:absolute;left:100px;top:34px;font-size:13px;color:var(--orange)}
.job .dot{position:absolute;left:371px;top:6px;width:23px;height:23px;border-radius:50%;background:var(--orange)}
.job .detail{position:absolute;left:458px;width:380px}
.job .detail h4{font-size:15px;font-weight:800}
.job .detail .loc{position:absolute;left:262px;top:0;font-size:13px;color:var(--muted);display:flex;align-items:center;gap:6px}
.job .detail .loc svg{width:12px;height:12px;fill:var(--orange)}
.job .detail p{font-size:12.5px;line-height:1.6;color:var(--muted);margin-top:12px;width:240px}
.section-title{position:absolute;left:0;width:1200px;text-align:center;font-size:32px;font-weight:800;letter-spacing:1px}
.skills{position:absolute;top:2210px;left:0;width:1200px;height:180px}
.skill{position:absolute;top:0;width:180px;height:180px;text-align:center}
.skill svg{position:absolute;left:0;top:0}
.skill .num{position:absolute;top:44px;width:100%;font-size:54px;color:var(--ink)}
.skill .lbl{position:absolute;top:112px;width:100%;font-size:13px;color:var(--muted)}
.portfolio{top:2470px;height:500px}
.shots{position:absolute;left:30px;top:176px;display:flex;gap:4px}
.shot{width:284px;height:252px}
.shot:nth-child(1){background:linear-gradient(135deg,#6d6150,#a58c78 50%,#4f4a44)}
.shot:nth-child(2){background:linear-gradient(135deg,#4e5b56,#b49888 50%,#585f5a)}
.shot:nth-child(3){background:linear-gradient(135deg,#d8d4cc,#8a7e70 50%,#3e3a36)}
.touch{position:absolute;top:3180px;left:145px;width:910px}
.touch .photo{position:absolute;left:0;top:10px;width:126px;height:126px;background:linear-gradient(160deg,#8a8a8a,#3c3c3c)}
.touch .copy{position:absolute;left:176px;top:0;width:734px}
.touch h3{font-size:30px;font-weight:800}
.touch .tagline{font-size:17px;margin-top:16px}
.touch p.body{font-size:14px;line-height:1.75;color:var(--muted);margin-top:26px}
.touch .contact{justify-content:flex-start;margin-top:30px}
.touch .social{justify-content:flex-start;margin-top:26px}
.touch .btn{margin-top:28px}
.footer{position:absolute;left:0;top:3780px;width:1200px;height:84px;background:var(--navy);color:var(--white);font-size:13px;display:flex;align-items:center;justify-content:center}
.footer .page{position:absolute;right:30px;font-size:12px;opacity:.8}
</style>
</head>
<body>
<header class="hero" role="img" aria-label="Team photo banner with navy overlay">
  <span class="btn">Download my resume <svg viewBox="0 0 14 14"><path d="M6 1h2v6h3L7 11 3 7h3z" fill="#fff"/><rect x="2" y="12" width="10" height="1.5" fill="#fff"/></svg></span>
</header>
<div class="avatar" role="img" aria-label="Portrait photo of Daniel Storm"></div>

<section class="intro">
  <h1 class="name">DANIEL STORM</h1>
  <p class="tagline">I'm an independent software contractor, architect, tech trainer.</p>
  <p class="body">Lorem ipsum dolor sit amet, consectetur adipiscing elit, sed do eiusmod tempor incididunt ut labore et dolore magna aliqua. Quis ipsum suspendisse ultrices gravida commodo viverra maecenas accumsan lacus vel facilisis.</p>
  <p class="body" style="margin-top:18px">Sed ut perspiciatis unde omnis iste natus error sit voluptatem accusantium doloremque laudantium, totam rem aperiam, eaque ipsa quae ab illo inventore veritatis et quasi architecto beatae vitae dicta sunt explicabo. Nemo enim ipsam voluptatem quia voluptas sit aspernatur aut odit aut fugit, sed quia consequuntur magni dolores eos qui ratione voluptatem sequi nesciunt. Neque porro quisquam est, qui dolorem ipsum quia dolor sit amet, consectetur, adipisci velit, sed quia non numquam eius modi tempora incidunt ut labore et dolore magnam aliquam quaerat.</p>
  <div class="contact">
    <span><svg viewBox="0 0 18 18"><rect x="1" y="3" width="16" height="12" rx="1"/><path d="M1 4l8 6 8-6" stroke="#fff" stroke-width="1.5" fill="none"/></svg>info@danielstorm.com</span>
    <span><svg viewBox="0 0 18 18"><path d="M4 1l3 4-2 2c1 2 3 4 5 5l2-2 4 3-2 3C8 16 2 10 1 3z"/></svg>1 555 010 0199</span>
  </div>
  <div class="social"><i></i><i></i><i></i><i></i><i></i></div>
</section>

<section class="panel work">
  <h2 class="tab">WORK EXPERIENCES</h2>
  <div class="timeline">
    <div class="axis"></div>
    <div class="job" style="top:160px"><div class="role">Software contractor</div><div class="dates">Sep 2016 - Present</div><div class="dot"></div><div class="detail"><h4>Lorem ipsum dolo</h4><span class="loc"><svg viewBox="0 0 12 12"><path d="M6 0a4 4 0 0 1 4 4c0 3-4 8-4 8S2 7 2 4a4 4 0 0 1 4-4z"/></svg>Lorem ipsum</span><p>Lorem ipsum dolor sit amet, consectetur adipiscing elit, sed do eiusmod tempor incididunt ut labore.</p></div></div>
    <div class="job" style="top:320px"><div class="role">Software architect</div><div class="dates">Sep 2013 - Feb 2016</div><div class="dot"></div><div class="detail"><h4>Lorem ipsum dolo</h4><span class="loc"><svg viewBox="0 0 12 12"><path d="M6 0a4 4 0 0 1 4 4c0 3-4 8-4 8S2 7 2 4a4 4 0 0 1 4-4z"/></svg>Lorem ipsum</span><p>Lorem ipsum dolor sit amet, consectetur adipiscing elit, sed do eiusmod tempor.</p></div></div>
    <div class="job" style="top:472px"><div class="role">Ullamco laboris</div><div class="dates">Sep 2010 - Feb 2013</div><div class="dot"></div><div class="detail"><h4>Lorem ipsum dolo</h4><span class="loc"><svg viewBox="0 0 12 12"><path d="M6 0a4 4 0 0 1 4 4c0 3-4 8-4 8S2 7 2 4a4 4 0 0 1 4-4z"/></svg>Lorem ipsum</span><p>Lorem ipsum dolor sit amet, consectetur adipiscing elit, sed do eiusmod tempor incididunt ut labore et dolore magna aliqua.</p></div></div>
    <div class="job" style="top:640px"><div class="role">Duis aute irure</div><div class="dates">Sep 2008 - Present</div><div class="dot"></div><div class="detail"><h4>Lorem ipsum dolo</h4><span class="loc"><svg viewBox="0 0 12 12"><path d="M6 0a4 4 0 0 1 4 4c0 3-4 8-4 8S2 7 2 4a4 4 0 0 1 4-4z"/></svg>Lorem ipsum</span><p>Lorem ipsum dolor sit amet, consectetur adipiscing elit, sed do eiusmod tempor incididunt.</p></div></div>
    <div class="job" style="top:804px"><div class="role">Excepteur sint</div><div class="dates">Sep 2005 - Feb 2008</div><div class="dot"></div><div class="detail"><h4>Lorem ipsum dolo</h4><span class="loc"><svg viewBox="0 0 12 12"><path d="M6 0a4 4 0 0 1 4 4c0 3-4 8-4 8S2 7 2 4a4 4 0 0 1 4-4z"/></svg>Lorem ipsum</span><p>Lorem ipsum dolor sit amet, consectetur adipiscing elit, sed do eiusmod tempor incididunt ut labore et dolore.</p></div></div>
    <div class="job" style="top:952px"><div class="role">Software Tech trainer</div><div class="dates">Sep 2000 - Feb 2005</div><div class="dot"></div><div class="detail"><h4>Lorem ipsum dolo</h4><span class="loc"><svg viewBox="0 0 12 12"><path d="M6 0a4 4 0 0 1 4 4c0 3-4 8-4 8S2 7 2 4a4 4 0 0 1 4-4z"/></svg>Lorem ipsum</span><p>Lorem ipsum dolor sit amet, consectetur adipiscing elit, sed do eiusmod tempor incididunt ut labore et dolore.</p></div></div>
  </div>
</section>

<h2 class="section-title" style="top:2108px">PROFESSIONAL SKILLS</h2>
<section class="skills">
  <div class="skill" style="left:280px"><svg width="180" height="180" viewBox="0 0 180 180"><circle cx="90" cy="90" r="85" fill="none" stroke="var(--ring)" stroke-width="6"/><circle cx="90" cy="90" r="85" fill="none" stroke="var(--orange)" stroke-width="6" stroke-dasharray="400 534" transform="rotate(-90 90 90)"/></svg><div class="num">75%</div><div class="lbl">Maecenas sit lectin</div></div>
  <div class="skill" style="left:510px"><svg width="180" height="180" viewBox="0 0 180 180"><circle cx="90" cy="90" r="85" fill="none" stroke="var(--ring)" stroke-width="6"/><circle cx="90" cy="90" r="85" fill="none" stroke="var(--orange)" stroke-width="6" stroke-dasharray="110 534" transform="rotate(-90 90 90)"/></svg><div class="num">9,358</div><div class="lbl">Aliquam erat volutpat</div></div>
  <div class="skill" style="left:740px"><svg width="180" height="180" viewBox="0 0 180 180"><circle cx="90" cy="90" r="85" fill="none" stroke="var(--ring)" stroke-width="6"/><circle cx="90" cy="90" r="85" fill="none" stroke="var(--orange)" stroke-width="6" stroke-dasharray="80 534" transform="rotate(-90 90 90)"/></svg><div class="num">12</div><div class="lbl">Proin dolor</div></div>
</section>

<section class="panel portfolio">
  <h2 class="tab" style="top:40px">PORTFOLIO</h2>
  <div class="shots">
    <div class="shot" role="img" aria-label="Group photo of a training class"></div>
    <div class="shot" role="img" aria-label="Portrait photo of Daniel Storm"></div>
    <div class="shot" role="img" aria-label="Photo of people in an office"></div>
  </div>
</section>

<h2 class="section-title" style="top:3062px">GET IN TOUCH</h2>
<section class="touch">
  <div class="photo" role="img" aria-label="Black and white portrait of Daniel Storm"></div>
  <div class="copy">
    <h3>Daniel Storm</h3>
    <p class="tagline">I'm an independent software contractor, architect, tech trainer.</p>
    <p class="body">Lorem ipsum dolor sit amet, consectetur adipiscing elit, sed do eiusmod tempor incididunt ut labore et dolore magna aliqua. Quis ipsum suspendisse ultrices gravida commodo viverra maecenas accumsan lacus vel facilisis.</p>
    <p class="body" style="margin-top:18px">Sed ut perspiciatis unde omnis iste natus error sit voluptatem accusantium doloremque laudantium, totam rem aperiam, eaque ipsa quae ab illo inventore veritatis et quasi architecto beatae vitae dicta sunt explicabo. Nemo enim ipsam voluptatem quia voluptas sit aspernatur aut odit aut fugit, sed quia consequuntur magni dolores eos qui ratione voluptatem sequi nesciunt. Neque porro quisquam est, qui dolorem ipsum quia dolor sit amet, consectetur, adipisci velit, sed quia non numquam eius modi tempora incidunt ut labore et dolore magnam aliquam quaerat.</p>
    <div class="contact">
      <span><svg viewBox="0 0 18 18"><rect x="1" y="3" width="16" height="12" rx="1"/><path d="M1 4l8 6 8-6" stroke="#fff" stroke-width="1.5" fill="none"/></svg>info@danielstorm.com</span>
      <span><svg viewBox="0 0 18 18"><path d="M4 1l3 4-2 2c1 2 3 4 5 5l2-2 4 3-2 3C8 16 2 10 1 3z"/></svg>1 555 010 0199</span>
    </div>
    <div class="social"><i></i><i></i><i></i><i></i><i></i></div>
    <span class="btn">Download my resume <svg viewBox="0 0 14 14"><path d="M6 1h2v6h3L7 11 3 7h3z" fill="#fff"/><rect x="2" y="12" width="10" height="1.5" fill="#fff"/></svg></span>
  </div>
</section>

<footer class="footer">Copyright © Daniel Storm All Rights reserved &nbsp;|&nbsp; Privacy Policy &nbsp;|&nbsp; Terms and Use<span class="page">1/8</span></footer>
</body>
</html>
```